MRT Property - Business Cards

Looking for a business card & general letterhead, signage etc design for our new logo.

Colours:
000a20
0056a2
00b5ef
0088ce
68cef2

Fonts:
Poppins
Karla

Please keep look and feel of new brand - example in the zip package I sent.

```html
<!DOCTYPE html>
<html lang="en">
<head>
<meta charset="utf-8">
<title>MRT Property – Business Cards</title>
<link rel="stylesheet" href="https://fonts.googleapis.com/css2?family=Poppins:wght@400;500;600&family=Kalam:wght@400&display=swap">
<style>
  :root {
    --navy: #000a20;
    --royal: #0056a2;
    --royal-deep: #0b55a3;
    --sky: #00b5ef;
    --ocean: #0088ce;
    --ice: #68cef2;
    --paper: #ffffff;
    --backdrop: #e9edf2;
    --ink: #1b2030;
  }
  * { margin: 0; padding: 0; box-sizing: border-box; }
  html, body { width: 900px; height: 1200px; overflow: hidden; }
  body {
    background: var(--backdrop);
    font-family: "Poppins", sans-serif;
    color: var(--ink);
    position: relative;
  }
  .card {
    position: absolute;
    border-radius: 22px;
    overflow: hidden;
    box-shadow: 0 6px 18px rgba(0, 10, 32, 0.25);
  }
  .card--front { left: 80px; top: 131px; width: 742px; height: 441px; background: var(--paper); }
  .card--back  { left: 78px; top: 638px; width: 744px; height: 440px; background: var(--royal-deep); }

  .front-wave { position: absolute; left: 0; top: 0; width: 742px; height: 441px; }

  .brand-name {
    position: absolute;
    font-family: "Poppins", sans-serif;
    font-weight: 600;
    white-space: nowrap;
    letter-spacing: 0.5px;
  }
  .card--front .brand-name { left: 78px; top: 200px; font-size: 31px; color: var(--royal); }
  .card--back .brand-name { right: 66px; top: 320px; font-size: 50px; color: var(--paper); }

  .divider {
    position: absolute; left: 348px; top: 97px;
    width: 2px; height: 224px; background: var(--royal);
  }
  .contact { position: absolute; left: 365px; top: 94px; }
  .contact__name {
    font-family: "Kalam", cursive;
    font-size: 30px; line-height: 1.1; color: var(--royal);
  }
  .contact__role { font-size: 14px; margin-top: 4px; }
  .contact__address { font-size: 14.5px; line-height: 22px; margin-top: 22px; }
  .contact__list { list-style: none; margin-top: 18px; }
  .contact__list li {
    display: flex; align-items: center; gap: 10px;
    font-size: 14.5px; height: 28px;
  }
  .contact__list svg { width: 15px; height: 15px; flex: none; }
</style>
</head>
<body>

<section class="card card--front" aria-label="Business card front">
  <svg class="front-wave" viewBox="0 0 742 441" aria-hidden="true">
    <path d="M0 322 C150 300 280 330 420 375 C560 420 680 380 742 340 L742 441 L0 441 Z" fill="var(--sky)"/>
    <path d="M0 340 C150 316 280 345 420 390 C560 432 680 395 742 360 L742 441 L0 441 Z" fill="var(--paper)"/>
    <path d="M420 392 C560 428 680 398 742 372 L742 441 L420 441 Z" fill="var(--ice)"/>
    <path d="M0 347 C160 322 290 355 430 400 C560 440 680 410 742 385 L742 441 L0 441 Z" fill="var(--royal-deep)"/>
  </svg>

  <div class="brand-name">MRT Property</div>

  <div class="divider"></div>

  <div class="contact">
    <div class="contact__name">Daniel Brooks</div>
    <div class="contact__role">Managing Director</div>
    <div class="contact__address">418 Maple Ridge Ave Suite<br>220 Dayton Ohio 45402</div>
    <ul class="contact__list">
      <li>
        <svg viewBox="0 0 24 24" aria-hidden="true"><path fill="var(--royal)" d="M6.6 10.8a15.1 15.1 0 0 0 6.6 6.6l2.2-2.2c.3-.3.7-.4 1-.2 1.1.4 2.3.6 3.6.6.6 0 1 .4 1 1V20c0 .6-.4 1-1 1A17 17 0 0 1 3 4c0-.6.4-1 1-1h3.5c.6 0 1 .4 1 1 0 1.3.2 2.5.6 3.6.1.3 0 .7-.2 1z"/></svg>
        1 (555) 214-7390
      </li>
      <li>
        <svg viewBox="0 0 24 24" aria-hidden="true"><path fill="var(--royal)" d="M2 5h20v14H2z"/><path fill="none" stroke="var(--paper)" stroke-width="1.8" d="M2.5 5.5 12 13l9.5-7.5"/></svg>
        hello@mrtproperty.com
      </li>
      <li>
        <svg viewBox="0 0 24 24" aria-hidden="true"><circle cx="12" cy="12" r="10" fill="var(--royal)"/><path fill="none" stroke="var(--paper)" stroke-width="1.4" d="M2 12h20M12 2c3 3 3 17 0 20M12 2c-3 3-3 17 0 20"/></svg>
        www.mrtproperty.com
      </li>
    </ul>
  </div>
</section>

<section class="card card--back" aria-label="Business card back">
  <div class="brand-name">MRT Property</div>
</section>

</body>
</html>
```